Business Cards for a law firm

Business cards for our law firm. Use our silhoette logo and OAK PARTNERS - check our website (www.oakpartners.example)

Contact Information for Business Card

our silhouette logo, OAK PARTNERS, 800-555-0147, Dorian Pemberton, dorian@oakpartners.example

Requirements
Must have
• our silhouette logo, OAK PARTNERS, 800-555-0147, Dorian Pemberton, dorian@oakpartners.example

```html
<!DOCTYPE html>
<html lang="en">
<head>
<meta charset="utf-8">
<title>Oak Partners — Business Cards</title>
<link rel="stylesheet" href="https://fonts.googleapis.com/css2?family=Montserrat:wght@400;500;600&family=Source+Sans+3:wght@700&display=swap">
<style>
  :root {
    --backdrop: #e6e6e6;
    --paper: #ffffff;
    --navy: #233168;
    --navy-deep: #1c2858;
    --ink: #1b1b1b;
  }
  * { box-sizing: border-box; margin: 0; padding: 0; }
  html, body { width: 1200px; height: 1108px; overflow: hidden; }
  body { background: var(--backdrop); position: relative; font-family: "Montserrat", sans-serif; }

  .card { position: absolute; }
  .card--front { left: 219px; top: 50px; width: 774px; height: 473px; background: var(--paper); }
  .card--back { left: 217px; top: 568px; width: 776px; height: 456px; background: var(--navy); }

  .brand { position: absolute; display: flex; align-items: center; }
  .brand__mark { background: var(--navy); }
  .brand__name { font-family: "Montserrat", sans-serif; font-weight: 600; color: var(--navy); white-space: nowrap; }

  .card--front .brand { left: 97px; top: 245px; }
  .card--front .brand__mark { width: 36px; height: 36px; margin-right: 10px; }
  .card--front .brand__name { font-size: 21px; letter-spacing: 2.2px; }

  .divider { position: absolute; left: 380px; top: 182px; width: 2px; height: 155px; background: var(--navy); }

  .person { position: absolute; left: 394px; top: 183px; }
  .person__name { font-family: "Source Sans 3", sans-serif; font-weight: 700; font-size: 32px; color: var(--navy); line-height: 1.1; }
  .person__role { font-size: 17px; color: var(--ink); margin-top: 2px; }

  .contacts { position: absolute; left: 394px; top: 255px; list-style: none; }
  .contacts li { display: flex; align-items: center; height: 30.5px; font-size: 17.5px; color: var(--ink); }
  .contacts svg { width: 17px; height: 17px; margin-right: 9px; fill: var(--navy); flex: none; }

  .card--back .brand { left: 80px; top: 202px; }
  .card--back .brand__mark { width: 78px; height: 78px; margin-right: 24px; background: var(--navy-deep); }
  .card--back .brand__name { font-size: 44px; letter-spacing: 4px; color: var(--navy-deep); }
</style>
</head>
<body>
  <section class="card card--front">
    <div class="brand">
      <span class="brand__mark"></span>
      <span class="brand__name">OAK PARTNERS</span>
    </div>
    <div class="divider"></div>
    <div class="person">
      <h1 class="person__name">Dorian Pemberton</h1>
      <p class="person__role">Lawyer</p>
    </div>
    <ul class="contacts">
      <li>
        <svg viewBox="0 0 24 24" aria-hidden="true"><path d="M6.6 10.8a15.1 15.1 0 0 0 6.6 6.6l2.2-2.2c.3-.3.7-.4 1-.2 1.1.4 2.3.6 3.6.6.6 0 1 .4 1 1V20c0 .6-.4 1-1 1C10.6 21 3 13.4 3 4c0-.6.4-1 1-1h3.5c.6 0 1 .4 1 1 0 1.3.2 2.5.6 3.6.1.3 0 .7-.2 1z"/></svg>
        800-555-0147
      </li>
      <li>
        <svg viewBox="0 0 24 24" aria-hidden="true"><path d="M3 6h18v2l-9 5.5L3 8z M3 10l9 5.5 9-5.5v8H3z"/></svg>
        dorian@oakpartners.example
      </li>
      <li>
        <svg viewBox="0 0 24 24" aria-hidden="true"><path d="M12 2a10 10 0 1 0 0 20 10 10 0 0 0 0-20zm0 2c1 0 2.3 2 2.8 5H9.2C9.7 6 11 4 12 4zM4.3 11h4.6c0 .7 0 1.3.1 2H4.3a8 8 0 0 1 0-2zm.6 4h4.4c.3 1.6.8 2.9 1.4 3.9A8 8 0 0 1 4.9 15zm4.4-6H4.9a8 8 0 0 1 5.8-3.9C10.1 6.1 9.6 7.4 9.3 9zM12 20c-1 0-2.3-2-2.8-5h5.6c-.5 3-1.8 5-2.8 5zm3-7h-6c-.1-.7-.1-1.3 0-2h6c.1.7.1 1.3 0 2zm-1.7 5.9c.6-1 1.1-2.3 1.4-3.9h4.4a8 8 0 0 1-5.8 3.9zM15.1 13c.1-.7.1-1.3.1-2h4.6a8 8 0 0 1 0 2zm-.4-4c-.3-1.6-.8-2.9-1.4-3.9A8 8 0 0 1 19.1 9z"/></svg>
        www.oakpartners.example
      </li>
    </ul>
  </section>

  <section class="card card--back">
    <div class="brand">
      <span class="brand__mark"></span>
      <span class="brand__name">OAK PARTNERS</span>
    </div>
  </section>
</body>
</html>
```